Islamic App which helps to calculate, track and pay Zakat

We need an application which helps muslim people to calculate and pay Zakat - mandatory donations which muslim should pay based on his income. The application will consist of two parts (applications) - the one which is used by "payer" and another one - used by "receiver". To make a payment "payer" will scan QR-code which "receiver" will generate in his app and show to payer. "Receiver" will have option to initiate cash withdrawal once he collected required minimum for the withdrawal.
Important that "payer" side journey to make a payment should be as short as possible - imaging same as you make donation by cash - you just gave money and left, similar experience should be with app - couple-three taps to make it. For receiver side major requirement is to keep the UI/UX as simple as possible, these guys usually are not aware about online payments (roughly speaking this part of the app should be more similar to Quillotap rather than to banking/financial app)
In this Figma I tried to sketch the UX for both sides (just to explain the idea): https://www.plovix.com/file/Rt4mWq8ZpLbN2vKe7sJd3X/Plovix-basics?type=design&node-id=2741-583016&mode=design

Target Market(s)

Muslims

Industry/Entity Type

Donations

Colors
0094D4
00A9DD
6FCCEA
C7EBF8
E9F6FB
00AB8E
00BBA5
67D7C9
C6EFE9
E9F9F6

Requirements
Must have
• The application should have soul. Design should show that this application intend to help people, not just money transfer
Nice to have
• Payment should be as quick as possible, in the sketches I showed it as banknotes/coins which user need to slide-up to pay. Maybe make it similar as Vel OS dock icons?
Should not have
• The application should not look as banking/financial app or wallet app

```html
<!DOCTYPE html>
<html lang="en">
<head>
<meta charset="utf-8">
<title>Zakat App Screens</title>
<link href="https://fonts.googleapis.com/css2?family=Roboto:wght@300;400;500;700&display=swap" rel="stylesheet">
<style>
  :root{
    --brand:#3d5ab8;
    --ink:#1d1d1f;
    --muted:#9a9a9a;
    --key-border:#e2e3e6;
    --dot:#f1f2f4;
    --white:#ffffff;
    --photo-sky:#a9c6da;
    --photo-mid:#c9b79b;
    --photo-ground:#e4dccd;
  }
  *{box-sizing:border-box;margin:0;padding:0}
  html,body{width:1200px;height:763px;overflow:hidden}
  body{background:var(--brand);font-family:'Roboto',sans-serif;color:var(--ink);position:relative}
  .screen{position:absolute;top:72px;width:285px;height:617px;background:var(--white);border-radius:30px;overflow:hidden}
  .screen--signin{left:86px}
  .screen--code{left:461px}
  .screen--profile{left:835px}
  .wordmark{position:absolute;left:0;width:100%;text-align:center;font-weight:700;font-size:42px;color:var(--brand);letter-spacing:.5px}
  .title{position:absolute;top:158px;width:100%;text-align:center;font-size:20px;font-weight:400}
  .phone-field{position:absolute;left:55px;top:208px;width:172px;font-size:19px;font-weight:300;border-bottom:1px solid #cfcfcf;padding-bottom:6px;white-space:nowrap}
  .phone-field .placeholder{color:var(--muted)}
  .hint{position:absolute;left:56px;top:247px;font-size:8px}
  .subtitle{position:absolute;top:189px;width:100%;text-align:center;font-size:11px;line-height:19px}
  .btn{position:absolute;left:37px;width:211px;height:36px;border-radius:18px;background:var(--brand);color:var(--white);font-weight:500;font-size:15px;display:flex;align-items:center;justify-content:center}
  .code-dots{position:absolute;top:247px;left:41px;display:flex;gap:10px}
  .code-dots span{width:44px;height:44px;border-radius:50%;background:var(--dot)}
  .keypad{position:absolute;left:41px;top:377px;display:grid;grid-template-columns:repeat(3,60px);column-gap:12px;row-gap:12px}
  .key{height:34px;border:1.5px solid var(--key-border);border-radius:7px;display:flex;align-items:center;justify-content:center;font-size:12px;font-weight:300;color:#444}
  .home-bar{position:absolute;left:50px;bottom:26px;width:185px;height:7px;border-radius:4px;background:#111}
  .photo{position:absolute;left:0;top:0;width:100%;height:451px;background:linear-gradient(180deg,var(--photo-sky) 0%,#d6d2c6 45%,var(--photo-mid) 62%,var(--photo-ground) 100%)}
  .edit-btn{position:absolute;left:18px;top:46px;width:30px;height:29px;border-radius:6px;background:var(--white);display:flex;align-items:center;justify-content:center}
  .side-tab{position:absolute;left:245px;top:236px;width:80px;height:80px;border-radius:50%;background:var(--brand);display:flex;align-items:center;padding-left:14px}
  .profile-card{position:absolute;left:18px;top:410px;width:247px;height:140px;background:var(--white);border-radius:8px;padding:12px 22px}
  .profile-card h2{font-size:24px;font-weight:700;margin-bottom:6px}
  .profile-card p{font-size:12.5px;line-height:19px;color:#333}
  .amount{position:absolute;left:22px;top:94px;display:flex;align-items:baseline;gap:6px}
  .amount .value{font-size:35px;font-weight:500;color:var(--brand)}
  .amount .currency{font-size:18px;font-weight:500}
  .print-btn{position:absolute;left:191px;top:97px;width:34px;height:34px;border-radius:50%;background:var(--brand);display:flex;align-items:center;justify-content:center}
</style>
</head>
<body>

<section class="screen screen--signin">
  <div class="wordmark" style="top:58px">Zakat</div>
  <h1 class="title">Sign in to Zakat App</h1>
  <div class="phone-field">+971 <span class="placeholder">(50) 000-00-00</span></div>
  <p class="hint">Please enter your UAE phone number</p>
  <div class="btn" style="top:293px">NEXT</div>
  <div class="keypad">
    <div class="key">1</div><div class="key">2</div><div class="key">3</div>
    <div class="key">4</div><div class="key">5</div><div class="key">6</div>
    <div class="key">7</div><div class="key">8</div><div class="key">9</div>
    <div class="key">+*#</div><div class="key">0</div>
    <div class="key"><svg width="9" height="9" viewBox="0 0 9 9"><path d="M1 1l7 7M8 1L1 8" stroke="#444" stroke-width="2"/></svg></div>
  </div>
  <div class="home-bar"></div>
</section>

<section class="screen screen--code">
  <div class="wordmark" style="top:58px">Zakat</div>
  <h1 class="title">Input Code</h1>
  <p class="subtitle">We have sent an SMS with a 4digit<br>code to phone +971 50 7160384</p>
  <div class="code-dots"><span></span><span></span><span></span><span></span></div>
  <div class="btn" style="top:316px">SIGN IN</div>
  <div class="keypad">
    <div class="key">1</div><div class="key">2</div><div class="key">3</div>
    <div class="key">4</div><div class="key">5</div><div class="key">6</div>
    <div class="key">7</div><div class="key">8</div><div class="key">9</div>
    <div class="key">+*#</div><div class="key">0</div>
    <div class="key"><svg width="9" height="9" viewBox="0 0 9 9"><path d="M1 1l7 7M8 1L1 8" stroke="#444" stroke-width="2"/></svg></div>
  </div>
  <div class="home-bar"></div>
</section>

<section class="screen screen--profile">
  <div class="photo" role="img" aria-label="Photo of a pilgrim in a robe walking toward the Kaaba in the courtyard of the Grand Mosque, minarets under a pale sky"></div>
  <div class="edit-btn">
    <svg width="16" height="16" viewBox="0 0 16 16" fill="none" stroke="var(--brand)" stroke-width="1.6"><path d="M7 3H3v10h10V9"/><path d="M12 2l2 2-6 6H6V8z"/></svg>
  </div>
  <div class="wordmark" style="top:36px">Zakat</div>
  <div class="side-tab">
    <svg width="18" height="16" viewBox="0 0 18 16" fill="none" stroke="#fff" stroke-width="2"><path d="M9 2L3 8l6 6M15 2L9 8l6 6"/></svg>
  </div>
  <div class="profile-card">
    <h2>Kamran</h2>
    <p>I am from Pakistan.<br>I have three kids.</p>
    <div class="amount"><span class="value">847</span><span class="currency">AED</span></div>
    <div class="print-btn">
      <svg width="18" height="16" viewBox="0 0 18 16" fill="none" stroke="#fff" stroke-width="1.8"><rect x="5" y="1" width="8" height="4"/><rect x="1" y="5" width="16" height="7" rx="2"/><rect x="5" y="9" width="8" height="6" fill="var(--brand)"/></svg>
    </div>
  </div>
  <div class="home-bar"></div>
</section>

</body>
</html>
```